Belmont Ridge Business Card Design Project

We have recently rebranded and would like to design new business cards that incorporate the corporate logo - double sided cards with corporate logo on one side and contact details on the other

Target Market(s)

Sophisticated and high net worth investors and finance industry professionals

Industry/Entity Type

Funds Management

Contact Information for Business Card

The card should prominently feature the company name and logo. Other details will be standard contact details for each staff member - name, address, phone, email, website

Colors
0054AA
0677BA
7BADD7
CADEEF
E8F1F8

Requirements
Must have
• Double-sided design with one side prominently featuring the corporate logo and the other side with all standard contact details

```html
<!DOCTYPE html>
<html lang="en">
<head>
<meta charset="utf-8">
<title>Belmont Ridge Business Card</title>
<link href="https://fonts.googleapis.com/css2?family=Cinzel:wght@600&family=Tinos:wght@700&family=Arimo:wght@400&display=swap" rel="stylesheet">
<style>
  :root {
    --navy: #184675;
    --ink: #333333;
    --paper: #ffffff;
    --backdrop: #9a9a9a;
  }
  * { margin: 0; padding: 0; box-sizing: border-box; }
  html, body { width: 1200px; height: 1059px; overflow: hidden; }
  body { background: var(--backdrop); position: relative; font-family: "Arimo", Arial, sans-serif; }

  .card { position: absolute; border-radius: 22px; overflow: hidden; }
  .card-front { left: 256px; top: 89px; width: 688px; height: 390px; background: var(--paper); }
  .card-back { left: 253px; top: 569px; width: 695px; height: 394px; background: var(--navy); }

  .wordmark { position: absolute; font-family: "Cinzel", "Times New Roman", serif; font-weight: 600; white-space: nowrap; letter-spacing: 0.5px; }
  .card-front .wordmark { left: 40px; top: 208px; font-size: 31px; color: var(--navy); }

  .divider { position: absolute; left: 344px; top: 109px; width: 1.5px; height: 173px; background: var(--navy); }

  .contact { position: absolute; left: 372px; top: 102px; color: var(--ink); }
  .contact-name { font-family: "Tinos", "Times New Roman", serif; font-weight: 700; font-size: 24px; color: var(--navy); letter-spacing: 0.3px; line-height: 28px; }
  .contact-role { font-size: 16.5px; line-height: 20px; margin-top: -2px; }
  .contact-address { font-size: 16.5px; line-height: 20.5px; margin-top: 12px; }
  .contact-list { list-style: none; margin-top: 14px; }
  .contact-list li { font-size: 16.5px; line-height: 25.5px; display: flex; align-items: center; gap: 7px; }
  .contact-list svg { width: 13px; height: 13px; flex: none; }

  .card-back .mark-dot { position: absolute; left: 84px; top: 177px; width: 62px; height: 62px; border-radius: 50%; background: var(--paper); }
  .card-back .wordmark { left: 226px; top: 185px; font-size: 45px; color: var(--paper); }
</style>
</head>
<body>

<section class="card card-front">
  <div class="wordmark">Belmont Ridge</div>
  <div class="divider"></div>
  <div class="contact">
    <div class="contact-name">DANIEL HAYES</div>
    <div class="contact-role">CEO/Founder</div>
    <div class="contact-address">Po Box 4120 Harbour Lane<br>Westfield AB 3197</div>
    <ul class="contact-list">
      <li>
        <svg viewBox="0 0 16 16" aria-hidden="true"><path fill="#184675" d="M3.5 1.5l2.3 2.6-1.3 1.7c.9 2 2.6 3.7 4.6 4.6l1.7-1.3 2.6 2.3-1.4 2.1C7 13.3 2.7 9 1.4 3z"/></svg>
        (555) 214-7730
      </li>
      <li>
        <svg viewBox="0 0 16 16" aria-hidden="true"><rect x="1" y="3" width="14" height="10" rx="1" fill="#184675"/><path d="M1.5 4l6.5 5 6.5-5" stroke="#fff" stroke-width="1.3" fill="none"/></svg>
        info@belmontridge.com
      </li>
      <li>
        <svg viewBox="0 0 16 16" aria-hidden="true" fill="none" stroke="#184675" stroke-width="1.3"><circle cx="8" cy="8" r="6.5"/><ellipse cx="8" cy="8" rx="3" ry="6.5"/><path d="M1.5 8h13M2.5 4.8h11M2.5 11.2h11"/></svg>
        www.belmontridge.com
      </li>
    </ul>
  </div>
</section>

<section class="card card-back">
  <div class="mark-dot"></div>
  <div class="wordmark">Belmont Ridge</div>
</section>

</body>
</html>
```